Dental practice logo either "Dental Lumora Centre" or "Dental Lumora Centre"

Dental practice with either of the logos mentioned above as we haven't decided on the name depends on which one looks better. Our motto of the practice is to create beautiful smiles and perform general dentistry.
Dr Oskar Velindre
47 Marlowby Road
Deeragun
Queensland 4814 and also the contact number, email address and website.
On the backside of the card it should be about the next appointment and also mention on the bottom" If unable to keep an appointment kindly give 24 hours notice otherwise a fee will be charged for the time reserved.
Reason: As it may take longer to design
We want the business card only on the dental practice named Dental Lumora Centre and with a caption underneath the practice name as "Townsville's home of dentistry"
Target Market(s)
dental patients and general population who want beautiful smile
Industry/Entity Type
Dental
Look and feel
Each slider illustrates characteristics of the customer's brand and the style your logo design should communicate.

```html
<!DOCTYPE html>
<html lang="en">
<head>
<meta charset="utf-8">
<title>Dental Lumora Centre – Business Card</title>
<link href="https://fonts.googleapis.com/css2?family=Open+Sans:wght@400;600;700&display=swap" rel="stylesheet">
<style>
  :root {
    --backdrop: #9a9a9a;
    --card: #ffffff;
    --card-shade: #f2f2f2;
    --ink: #1c1c1c;
    --ink-soft: #3a3a3a;
    --ink-muted: #5c5c5c;
    --accent: #f05a22;
    --accent-warm: #f7931e;
    --tab: #1f1f1f;
    --rule: #c9c9c9;
  }
  * { box-sizing: border-box; margin: 0; padding: 0; }
  html, body { width: 1200px; height: 894px; overflow: hidden; }
  body {
    background: var(--backdrop);
    font-family: "Open Sans", Arial, sans-serif;
    color: var(--ink);
  }
  .canvas { position: relative; width: 1200px; height: 894px; overflow: hidden; }
  .card {
    position: absolute;
    left: 240px;
    width: 720px;
    height: 411px;
    overflow: hidden;
    background: var(--card);
  }
  .card--front { top: 24px; }
  .card--back {
    top: 459px;
    background: linear-gradient(160deg, var(--card) 0%, var(--card-shade) 100%);
  }

  /* Brand lockup */
  .brand { position: absolute; display: flex; align-items: center; }
  .brand__dot { flex: none; border-radius: 50%; background: var(--accent); }
  .brand__text { display: flex; flex-direction: column; }
  .brand__name {
    font-weight: 600;
    text-transform: uppercase;
    color: var(--ink);
    line-height: 1.02;
    letter-spacing: 0.01em;
  }
  .brand__tagline { color: var(--ink-muted); margin-top: 6px; }
  .card--front .brand { left: 60px; right: 90px; top: 40px; justify-content: center; gap: 16px; }
  .card--front .brand__dot { width: 60px; height: 60px; }
  .card--front .brand__name { font-size: 30px; }
  .card--front .brand__tagline { font-size: 14px; }
  .card--back .brand { left: 392px; top: 44px; gap: 12px; }
  .card--back .brand__dot { width: 44px; height: 44px; }
  .card--back .brand__name { font-size: 21px; }
  .card--back .brand__tagline { font-size: 12px; margin-top: 4px; }

  /* Edge trims */
  .edge-strip {
    position: absolute; top: 0; bottom: 0; width: 14px;
    background: linear-gradient(180deg, var(--accent-warm), var(--accent));
  }
  .edge-tab { position: absolute; background: var(--tab); }
  .card--front .edge-strip { right: 0; }
  .card--front .edge-tab {
    right: 0; top: 150px; width: 46px; height: 190px;
    border-radius: 16px 0 0 16px;
  }
  .card--back .edge-strip { left: 0; }
  .card--back .edge-tab {
    left: 0; top: 36px; width: 44px; height: 150px;
    border-radius: 0 16px 16px 0;
    display: flex; flex-direction: column; justify-content: space-around; align-items: center;
    padding: 12px 0 12px 4px;
  }
  .icon { width: 18px; height: 18px; fill: none; stroke: #ffffff; stroke-width: 1.8; stroke-linecap: round; stroke-linejoin: round; }

  /* Appointment side */
  .appointment { position: absolute; left: 60px; right: 90px; top: 150px; }
  .appointment__title {
    font-size: 18px; font-weight: 700; color: var(--accent);
    text-transform: uppercase; letter-spacing: 0.08em; margin-bottom: 18px;
  }
  .appointment__row { display: flex; gap: 28px; margin-bottom: 20px; }
  .appointment__field { flex: 1; display: flex; align-items: flex-end; gap: 10px; font-size: 15px; color: var(--ink-soft); }
  .appointment__line { flex: 1; height: 22px; border-bottom: 1px solid var(--rule); }
  .notice {
    position: absolute; left: 60px; right: 90px; bottom: 26px;
    font-size: 12px; line-height: 17px; color: var(--ink-muted); text-align: center;
  }

  /* Contact side */
  .contact-list {
    position: absolute; left: 64px; top: 44px; list-style: none;
    font-size: 17px; line-height: 35px; color: var(--ink-soft);
  }
  .holder { position: absolute; left: 64px; top: 232px; }
  .holder__name { font-size: 21px; font-weight: 700; color: var(--ink-soft); }
  .holder__role { font-size: 14px; color: var(--ink-muted); margin-top: 2px; }
  .divider {
    position: absolute; left: 372px; top: 120px; width: 1px; height: 250px;
    background: linear-gradient(180deg, var(--rule), rgba(201,201,201,0));
  }
  .address {
    position: absolute; left: 392px; top: 282px;
    font-size: 15px; line-height: 22px; color: var(--ink-soft); font-style: normal;
  }
  .website {
    position: absolute; left: 392px; top: 350px;
    font-size: 15px; letter-spacing: 0.12em; color: var(--ink-soft);
  }
  .website strong { font-weight: 700; }
</style>
</head>
<body>
<main class="canvas">

  <section class="card card--front" aria-label="Business card appointment side">
    <div class="brand">
      <span class="brand__dot"></span>
      <div class="brand__text">
        <span class="brand__name">Dental Lumora<br>Centre</span>
        <span class="brand__tagline">Townsville's home of dentistry</span>
      </div>
    </div>

    <div class="appointment">
      <p class="appointment__title">Your next appointment</p>
      <div class="appointment__row">
        <span class="appointment__field">Date <span class="appointment__line"></span></span>
        <span class="appointment__field">Time <span class="appointment__line"></span></span>
      </div>
      <div class="appointment__row">
        <span class="appointment__field">With <span class="appointment__line"></span></span>
      </div>
    </div>

    <p class="notice">If unable to keep an appointment kindly give 24 hours notice, otherwise a fee will be charged for the time reserved.</p>

    <span class="edge-strip"></span>
    <span class="edge-tab"></span>
  </section>

  <section class="card card--back" aria-label="Business card contact side">
    <span class="edge-strip"></span>
    <div class="edge-tab">
      <svg class="icon" viewBox="0 0 24 24" aria-hidden="true"><path d="M5 3h4l2 5-2.5 1.5a11 11 0 0 0 6 6L16 13l5 2v4a2 2 0 0 1-2 2A17 17 0 0 1 3 5a2 2 0 0 1 2-2z"/></svg>
      <svg class="icon" viewBox="0 0 24 24" aria-hidden="true"><rect x="7" y="2" width="10" height="20" rx="2"/><path d="M11 18h2"/></svg>
      <svg class="icon" viewBox="0 0 24 24" aria-hidden="true"><rect x="4" y="9" width="16" height="9" rx="1"/><path d="M7 9V3h10v6M7 14h10v7H7z"/></svg>
      <svg class="icon" viewBox="0 0 24 24" aria-hidden="true"><rect x="3" y="5" width="18" height="14" rx="1"/><path d="M3 6l9 7 9-7"/></svg>
    </div>

    <ul class="contact-list">
      <li>(07) 5550 1427</li>
      <li>0400 555 318</li>
      <li>(07) 5550 1428</li>
      <li>hello@dentallumora.com.au</li>
    </ul>

    <div class="holder">
      <p class="holder__name">Dr Oskar Velindre</p>
      <p class="holder__role">General &amp; Cosmetic Dentist</p>
    </div>

    <div class="brand">
      <span class="brand__dot"></span>
      <div class="brand__text">
        <span class="brand__name">Dental Lumora<br>Centre</span>
        <span class="brand__tagline">Townsville's home of dentistry</span>
      </div>
    </div>

    <span class="divider"></span>

    <address class="address">47 Marlowby Road, Deeragun<br>Queensland 4814</address>
    <p class="website">www.<strong>dentallumora</strong>.com.au</p>
  </section>

</main>
</body>
</html>
```